Veluxa Bone & Motion Business Card

Need a business card using the logo provided. I want brand side of the card to be grey with the logo in the center of the card in white.

On the other side I leave to the designers

Target Market(s)

Personal Injury Attorneys

Industry/Entity Type

Medical

Contact Information for Business Card

Name, CEO. Cell Phone, (Hialeah, Address, Phone) (Homestead, Address, Phone) (Tallahassee, Address, Phone)

Colors

Designer to choose only greyscale colors for use in the design.

Requirements
Must have
• Logo by itself on one side

```html
<!DOCTYPE html>
<html lang="en">
<head>
<meta charset="utf-8">
<title>Veluxa Bone &amp; Motion – Business Card</title>
<link rel="stylesheet" href="https://fonts.googleapis.com/css2?family=Source+Sans+3:wght@400;600;700&display=swap">
<style>
  :root {
    --backdrop: #e8e8e8;
    --brand-slate: #8fa7b0;
    --card-white: #f2f2f3;
    --ink: #1d1f21;
    --divider: #b9bfc2;
    --band-grey: #6c7073;
  }
  * { box-sizing: border-box; margin: 0; padding: 0; }
  html, body { width: 1200px; height: 1200px; overflow: hidden; }
  body {
    background: var(--backdrop);
    font-family: "Source Sans 3", sans-serif;
    position: relative;
  }
  .card {
    position: absolute;
    left: 264px;
    width: 681px;
    height: 390px;
    border-radius: 32px;
    overflow: hidden;
  }
  /* Brand side */
  .card--brand { top: 165px; background: var(--brand-slate); }
  .brand-decoration {
    position: absolute;
    right: 12px; top: 0;
    width: 124px; height: 390px;
    border-radius: 0 0 40px 40px;
    background: linear-gradient(180deg, rgba(255,255,255,0.2), rgba(255,255,255,0.08) 65%, rgba(255,255,255,0));
  }
  .wordmark {
    position: absolute;
    left: 0; right: 0;
    text-align: center;
    font-weight: 600;
    color: #ffffff;
    line-height: 1;
  }
  .wordmark__name { top: 134px; font-size: 82px; letter-spacing: 15px; padding-left: 15px; }
  .wordmark__sub { top: 219px; font-size: 34px; letter-spacing: 8px; padding-left: 8px; }

  /* Contact side */
  .card--contact { top: 654px; height: 387px; background: var(--card-white); }
  .identity {
    position: absolute;
    right: 379px; top: 112px;
    text-align: right;
  }
  .identity__name, .identity__sub {
    font-weight: 600;
    color: var(--brand-slate);
    display: block;
    line-height: 1;
  }
  .identity__name { font-size: 44px; letter-spacing: 6px; margin-right: -6px; }
  .identity__sub { font-size: 20px; letter-spacing: 4px; margin-top: 10px; margin-right: -4px; }
  .person { margin-top: 30px; }
  .person__name { font-size: 21px; font-weight: 700; color: var(--brand-slate); line-height: 1.2; }
  .person__title { font-size: 16.5px; color: var(--ink); line-height: 1.35; }
  .person__cell { font-size: 16.5px; font-weight: 700; color: var(--ink); line-height: 1.35; display: inline-flex; align-items: center; gap: 8px; }
  .divider {
    position: absolute;
    left: 341px; top: 90px;
    width: 1px; height: 210px;
    background: var(--divider);
  }
  .locations {
    position: absolute;
    left: 381px; top: 84px;
    list-style: none;
  }
  .location {
    font-size: 16px;
    color: var(--ink);
    line-height: 19.7px;
    margin-bottom: 19.5px;
  }
  .location__phone { display: flex; align-items: center; gap: 6px; }
  .card-band {
    position: absolute;
    left: 0; bottom: 0;
    width: 100%; height: 11px;
    background: var(--brand-slate);
  }
  .card-band__end {
    position: absolute;
    right: 0; top: 0;
    width: 160px; height: 11px;
    background: var(--band-grey);
    clip-path: polygon(4px 0, 100% 0, 100% 100%, 0 100%);
  }
</style>
</head>
<body>

<section class="card card--brand" aria-label="Brand side">
  <div class="brand-decoration" role="img" aria-label="Faint brand decoration along the right edge"></div>
  <div class="wordmark wordmark__name">VELUXA</div>
  <div class="wordmark wordmark__sub">BONE &amp; MOTION</div>
</section>

<section class="card card--contact" aria-label="Contact side">
  <div class="identity">
    <span class="identity__name">VELUXA</span>
    <span class="identity__sub">BONE &amp; MOTION</span>
    <div class="person">
      <p class="person__name">Corinne Hallsey</p>
      <p class="person__title">Chief Executive Officer</p>
      <p class="person__cell">
        <svg width="11" height="18" viewBox="0 0 11 18" aria-hidden="true"><rect x="1" y="1" width="9" height="16" rx="1.8" fill="none" stroke="#8fa7b0" stroke-width="1.4"/><line x1="4" y1="14.5" x2="7" y2="14.5" stroke="#8fa7b0" stroke-width="1.2"/></svg>
        +1 555-210-4490
      </p>
    </div>
  </div>

  <div class="divider"></div>

  <ul class="locations">
    <li class="location">
      <span class="location__phone"><svg width="13" height="13" viewBox="0 0 24 24" aria-hidden="true"><path d="M6.6 10.8a15.1 15.1 0 0 0 6.6 6.6l2.2-2.2a1 1 0 0 1 1-.25 11.4 11.4 0 0 0 3.6.57 1 1 0 0 1 1 1V20a1 1 0 0 1-1 1A17 17 0 0 1 3 4a1 1 0 0 1 1-1h3.5a1 1 0 0 1 1 1c0 1.25.2 2.45.57 3.57a1 1 0 0 1-.25 1z" fill="#8fa7b0"/></svg>555-210-4401</span>
      412 Larkspur Lane<br>Brackenford, FL 4410
    </li>
    <li class="location">
      <span class="location__phone"><svg width="13" height="13" viewBox="0 0 24 24" aria-hidden="true"><path d="M6.6 10.8a15.1 15.1 0 0 0 6.6 6.6l2.2-2.2a1 1 0 0 1 1-.25 11.4 11.4 0 0 0 3.6.57 1 1 0 0 1 1 1V20a1 1 0 0 1-1 1A17 17 0 0 1 3 4a1 1 0 0 1 1-1h3.5a1 1 0 0 1 1 1c0 1.25.2 2.45.57 3.57a1 1 0 0 1-.25 1z" fill="#8fa7b0"/></svg>555-210-4402</span>
      88 Meridian Row<br>Ashmere, FL 4420
    </li>
    <li class="location">
      <span class="location__phone"><svg width="13" height="13" viewBox="0 0 24 24" aria-hidden="true"><path d="M6.6 10.8a15.1 15.1 0 0 0 6.6 6.6l2.2-2.2a1 1 0 0 1 1-.25 11.4 11.4 0 0 0 3.6.57 1 1 0 0 1 1 1V20a1 1 0 0 1-1 1A17 17 0 0 1 3 4a1 1 0 0 1 1-1h3.5a1 1 0 0 1 1 1c0 1.25.2 2.45.57 3.57a1 1 0 0 1-.25 1z" fill="#8fa7b0"/></svg>555-210-4403</span>
      730 Cypress Way<br>Pell Harbor, Florida 4430
    </li>
  </ul>

  <div class="card-band"><div class="card-band__end"></div></div>
</section>

</body>
</html>
```